Tom Parrish Acreage Services LLC

Need a business card design for a new company based in Cedar Hollow, MS. We specialize in under-brush clearing, forestry mulching, cutover mulching, right of way clearing, land line & fence row clearing, bush hogging, land clearing, wildlife food plots. We use compact track loaders and tractors. I will attach a picture of a compact track loader I would like to have on the card design if possible.

Target Market(s)

Businesses / Land Owners

Contact Information for Business Card

Tom Parrish
Owner / Operator

Cedar Hollow, MS

Call/Text: 601-555-0187
tpacreage@mailbrook.net
FB: @tomparrishacreageservicesllc

Font styles to use
Serif
Sans Serif

Requirements
Must have
• Contact info, city & state. Description of services.
Nice to have
• Not overwhelming back ground but eye and interest catching with clear objection of the business

```html
<!DOCTYPE html>
<html lang="en">
<head>
<meta charset="utf-8">
<title>Tom Parrish Acreage Services LLC – Business Card</title>
<link rel="stylesheet" href="https://fonts.googleapis.com/css2?family=Open+Sans:wght@400;600;700;800&display=swap">
<style>
  :root {
    --charcoal: #4a4a4c;
    --ink: #3a3a3c;
    --gold: #f3b92e;
    --orange: #f2a21c;
    --paper: #ffffff;
    --stage: #2a2a2b;
    --photo-a: #6f7a3a;
    --photo-b: #c9a12a;
  }
  * { box-sizing: border-box; margin: 0; padding: 0; }
  html, body { width: 1200px; height: 900px; overflow: hidden; background: var(--stage); }
  body { font-family: "Open Sans", Arial, sans-serif; }

  .card {
    position: absolute;
    left: 250px;
    width: 700px;
    height: 400px;
    background: var(--paper);
    overflow: hidden;
    box-shadow: 0 10px 30px rgba(0,0,0,.45);
  }
  .card--front { top: 35px; }
  .card--back { top: 465px; }
  .card__shapes { position: absolute; inset: 0; width: 700px; height: 400px; }

  .company {
    position: absolute; left: 34px; top: 20px;
    color: var(--paper); font-size: 24px; line-height: 1.2; font-weight: 400;
  }
  .company__lead { font-weight: 700; }
  .company__city { display: block; color: var(--gold); font-size: 21px; font-weight: 400; }

  .contact { position: absolute; right: 34px; top: 178px; text-align: right; color: var(--ink); }
  .contact__name { font-size: 34px; font-weight: 800; letter-spacing: .5px; line-height: 1; }
  .contact__title { color: var(--gold); font-size: 19px; font-weight: 600; margin-top: 4px; }
  .contact__list { list-style: none; margin-top: 16px; font-size: 16px; }
  .contact__item { display: flex; align-items: center; justify-content: flex-end; gap: 10px; height: 34px; }
  .contact__icon {
    width: 24px; height: 24px; border-radius: 50%; background: var(--gold);
    display: inline-flex; align-items: center; justify-content: center; flex: none;
  }

  .services { position: absolute; left: 40px; top: 30px; }
  .services__heading { font-size: 28px; font-weight: 800; color: var(--ink); letter-spacing: .5px; }
  .services__list { list-style: none; margin-top: 6px; }
  .services__item {
    font-size: 19px; font-weight: 800; color: var(--orange); line-height: 1.28; text-transform: uppercase;
  }
  .services__item::before {
    content: ""; display: inline-block; width: 7px; height: 7px; background: var(--ink);
    margin-right: 10px; vertical-align: middle; position: relative; top: -2px;
  }
</style>
</head>
<body>

<section class="card card--front" aria-label="Card front">
  <svg class="card__shapes" viewBox="0 0 700 400">
    <defs>
      <linearGradient id="loaderTones" x1="0" y1="0" x2="1" y2="1">
        <stop offset="0" stop-color="var(--photo-a)"/>
        <stop offset="1" stop-color="var(--photo-b)"/>
      </linearGradient>
    </defs>
    <polygon class="band-top" fill="var(--charcoal)" points="0,0 700,0 700,135 470,135 395,195 310,112 0,112"/>
    <polygon class="photo" role="img" aria-label="Photo of a yellow compact track loader with a mulcher head on grass" fill="url(#loaderTones)" points="0,128 300,128 380,210 330,400 0,400"/>
    <polygon class="band-bottom" fill="var(--gold)" points="345,400 385,312 440,368 700,368 700,400"/>
  </svg>

  <h1 class="company">
    <span class="company__lead">Tom Parrish</span> Acreage<br>
    Services LLC
    <span class="company__city">Cedar Hollow, MS</span>
  </h1>

  <div class="contact">
    <p class="contact__name">TOM PARRISH</p>
    <p class="contact__title">Owner / Operator</p>
    <ul class="contact__list">
      <li class="contact__item">601-555-0187
        <span class="contact__icon"><svg width="13" height="13" viewBox="0 0 24 24"><path fill="#fff" d="M6.6 10.8a15 15 0 0 0 6.6 6.6l2.2-2.2c.3-.3.7-.4 1-.2 1.1.4 2.3.6 3.6.6.6 0 1 .4 1 1V20c0 .6-.4 1-1 1A17 17 0 0 1 3 4c0-.6.4-1 1-1h3.5c.6 0 1 .4 1 1 0 1.3.2 2.5.6 3.6.1.3 0 .7-.2 1z"/></svg></span>
      </li>
      <li class="contact__item">tpacreage@mailbrook.net
        <span class="contact__icon"><svg width="14" height="12" viewBox="0 0 24 20"><rect x="2" y="2" width="20" height="13" rx="2" fill="none" stroke="#fff" stroke-width="2.4"/><path d="M8 19h8" stroke="#fff" stroke-width="2.4"/></svg></span>
      </li>
      <li class="contact__item">@tomparrishacreageservicesllc
        <span class="contact__icon"></span>
      </li>
    </ul>
  </div>
</section>

<section class="card card--back" aria-label="Card back">
  <svg class="card__shapes" viewBox="0 0 700 400">
    <defs>
      <linearGradient id="loaderTonesBack" x1="0" y1="0" x2="1" y2="1">
        <stop offset="0" stop-color="#5d5a2c"/>
        <stop offset="1" stop-color="var(--photo-b)"/>
      </linearGradient>
    </defs>
    <polygon class="band-side" fill="var(--charcoal)" points="560,0 700,0 700,400 600,400"/>
    <polygon class="chevron" fill="var(--gold)" points="470,190 700,190 700,300 640,300 560,240"/>
    <polygon class="photo" role="img" aria-label="Photo of a yellow compact track loader working among trees" fill="url(#loaderTonesBack)" points="0,300 150,300 230,250 320,310 585,310 585,400 0,400"/>
  </svg>

  <div class="services">
    <h2 class="services__heading">WE SPECIALIZE IN</h2>
    <ul class="services__list">
      <li class="services__item">Under-brush clearing</li>
      <li class="services__item">Forestry mulching</li>
      <li class="services__item">Right of way clearing</li>
      <li class="services__item">Land line &amp; fence row clearing</li>
      <li class="services__item">Bush hogging</li>
      <li class="services__item">Land clearing</li>
      <li class="services__item">Wildlife food plots</li>
    </ul>
  </div>
</section>

</body>
</html>
```